Sleek wordpress site for Bramblecrest finishing works

We are a commercial job shop that serves B2B, govt & LEO and retail clients.We need a wordpress site with 6 individual pages: homepage, coating, laser engraving, laser cutting, part marking, and contact us. I have attached an outline of the desired flow and sub headings for each page. I would like to incorporate the colors of the logo through out the site to be clean and sleek enough to appeal to B2B commercial clients yet be inviting enough for retail clients.

I would like to have easy picture functionality so photographs on each page can be updated easily.

Target Market(s)

B2B industrial & Govt and Military part marking, laser engraving and coating: machine shops, aerospace companies, tool manufactures. Retail: personalized gifts, Job Shop

Coding

Coded - Design and coding required

Font styles to use
Sans Serif
Other font styles liked:
• Open to suggestion

Colors
0255a3
3176b5
eaf1f7
cfdeed
ffffff

Requirements
Must have
• Clean easy to navigate flow, separate pages as indicated on attached outline, high class feel. Great picture functionality, professional and inviting feel,
• **update: needs to be optimized for mobile, should have a gallery function. Gallery can be an additional page or embedded
Nice to have
• Social media connectivity links,
Should not have
• crappy plugins that make back-end management difficult, no blog

```html
<!DOCTYPE html>
<html lang="en">
<head>
<meta charset="utf-8">
<title>Bramblecrest Finishing Works</title>
<link href="https://fonts.googleapis.com/css2?family=Exo+2:wght@500;600;700&family=Montserrat:ital,wght@0,400;0,500;0,600;0,700;1,400&display=swap" rel="stylesheet">
<style>
:root{
  --blue:#0255a3;
  --blue-mid:#3176b5;
  --blue-pale:#eaf1f7;
  --blue-soft:#cfdeed;
  --white:#ffffff;
  --ink:#1b1b1b;
  --text:#555555;
  --grey-bg:#ebebeb;
  --dark:#1f1f1f;
  --darker:#151515;
}
*{margin:0;padding:0;box-sizing:border-box}
html,body{width:1200px;height:4523px;overflow:hidden}
body{font-family:'Montserrat',sans-serif;color:var(--text);background:var(--white);position:relative}
.abs{position:absolute}
h2.section-title{font-family:'Exo 2',sans-serif;font-weight:600;color:var(--ink);font-size:42px;letter-spacing:1px;text-transform:uppercase}
.btn{display:flex;align-items:center;justify-content:center;background:var(--blue);color:var(--white);font-size:15px;font-weight:500;text-decoration:none}

/* header */
.site-header{top:0;left:0;width:1200px;height:136px;background:var(--white)}
.brand{left:150px;top:22px;display:flex;align-items:center;gap:12px;color:var(--blue);font-weight:700;font-size:17px;line-height:1.15;width:230px}
.brand-dot{width:40px;height:40px;border-radius:50%;background:var(--blue);flex:none}
.top-contact{top:18px;display:flex;align-items:center;gap:14px;font-size:15px;color:var(--blue)}
.icon-circle{width:36px;height:36px;border-radius:50%;background:var(--blue);display:flex;align-items:center;justify-content:center}
.top-social{top:26px;left:945px;display:flex;gap:22px}
.top-social span{width:14px;height:14px;border-radius:3px;background:#8a8a8a}
.main-nav{top:92px;left:377px;display:flex;gap:34px;font-size:14px;font-weight:600;color:#222;text-transform:uppercase}
.main-nav .active{color:var(--blue)}

/* hero */
.hero{top:136px;left:0;width:1200px;height:482px;background:linear-gradient(100deg,#3b3d44 0%,#23252b 30%,#4a3a36 60%,#7a3a1e 80%,#2a1a14 100%)}
.hero-title{top:105px;width:1200px;text-align:center;color:var(--white);font-family:'Exo 2',sans-serif;font-weight:600;font-size:52px;line-height:58px;text-transform:uppercase;letter-spacing:1px}
.hero-sub{top:236px;width:1200px;text-align:center;color:var(--white);font-size:26px;word-spacing:4px}
.hero .btn{top:316px;left:488px;width:227px;height:42px;font-size:15px;text-transform:uppercase}
.dots{top:424px;left:558px;display:flex;gap:10px}
.dots span{width:12px;height:12px;border-radius:50%;border:2px solid var(--white)}
.dots span.on{background:var(--white)}

/* partners */
.partners{top:618px;left:0;width:1200px;height:136px;background:var(--blue);display:flex;align-items:center;justify-content:space-around;padding:0 70px;color:var(--white);font-weight:700;font-size:22px}

/* about */
.about-title{top:845px;left:100px}
.about-text{top:930px;left:100px;width:533px;font-size:13px;line-height:30px}
.about-text p{margin-bottom:14px}
.about .btn{top:1240px;left:100px;width:132px;height:44px}
.about-photo{top:857px;left:663px;width:537px;height:515px;background:linear-gradient(135deg,#1c1a3a 0%,#3c3aa8 40%,#7a7bd8 55%,#2a2a55 80%,#111 100%)}

/* what we do */
.wwd-photo{top:1372px;left:0;width:663px;height:633px;background:linear-gradient(120deg,#3a1c10 0%,#b8561c 40%,#6b2e14 70%,#241612 100%)}
.wwd-box{top:1441px;left:72px;width:519px;height:494px;background:rgba(2,85,163,0.85);color:var(--white);text-align:center;padding:115px 60px 0}
.wwd-box h3{font-size:22px;font-weight:500;margin-bottom:34px}
.wwd-box p{font-size:13px;line-height:30px}
.wwd-box .btn-outline{display:inline-block;margin-top:22px;border:2px solid var(--white);padding:10px 26px;font-size:15px}
.wwd-title{top:1478px;right:100px}
.wwd-list{top:1560px;right:100px;text-align:right;list-style:none;font-size:14px;line-height:43px;color:#666}
.wwd-list li:first-child{color:var(--blue);text-decoration:underline}

/* why */
.why-title{top:2100px;width:1200px;text-align:center}
.why-intro{top:2198px;left:175px;width:850px;text-align:center;font-size:14px;line-height:36px}
.feature{width:300px;text-align:center}
.feature .icon{width:98px;height:98px;border-radius:50%;background:var(--blue);margin:0 auto 24px;display:flex;align-items:center;justify-content:center}
.feature h4{font-size:19px;font-weight:600;color:var(--ink);line-height:30px;margin-bottom:14px}
.feature p{font-size:13px;line-height:29px}

/* services */
.services{top:3082px;left:0;width:1200px;height:508px;background:var(--grey-bg)}
.services-title{top:102px;width:1200px;text-align:center}
.service-grid{top:189px;left:100px;display:flex;gap:8px}
.service{width:244px;height:205px;position:relative;background:linear-gradient(160deg,#2a2c34,#5a5f6a 50%,#1a1b20)}
.service:nth-child(2){background:linear-gradient(160deg,#0f2440,#3a6ea8 50%,#0a1420)}
.service:nth-child(3){background:linear-gradient(160deg,#1a1616,#8a3a22 50%,#1a1212)}
.service:nth-child(4){background:linear-gradient(160deg,#6a2a2a,#b8b8c0 50%,#3a3a44)}
.service span{position:absolute;left:0;right:0;bottom:14px;text-align:center;color:var(--white);font-size:22px;font-weight:600}

/* testimonials */
.test-title{top:3685px;width:1200px;text-align:center}
.quote-mark{top:3775px;font-family:Georgia,serif;font-size:90px;line-height:60px;color:#cccccc}
.test-text{top:3776px;left:195px;width:810px;text-align:center;font-style:italic;font-size:14px;line-height:34px;color:#777}
.avatar{top:3872px;left:552px;width:96px;height:96px;border-radius:50%;border:3px solid var(--blue);background:linear-gradient(180deg,#8a9aa8,#4a5561)}
.test-name{top:3988px;width:1200px;text-align:center;font-size:13px;color:#444;letter-spacing:1px}

/* contact bar */
.contact-bar{top:4100px;left:0;width:1200px;height:151px;background:var(--dark);color:#ddd;font-size:13px}
.contact-item{top:55px;display:flex;align-items:center;gap:22px;line-height:22px}
.contact-item .icon-circle{width:40px;height:40px}

/* footer */
.site-footer{top:4251px;left:0;width:1200px;height:272px;background:var(--darker);color:#ddd}
.footer-nav{top:55px;left:257px;display:flex;gap:22px;font-size:12px}
.footer-social{top:40px;left:800px;display:flex;gap:10px}
.footer-social span{width:40px;height:40px;border-radius:50%;border:2px solid #ddd}
.cert-title{top:112px;width:1200px;text-align:center;font-size:14px;font-weight:600;color:var(--white)}
.certs{top:155px;left:410px;display:flex;gap:70px}
.certs span{width:44px;height:44px;border-radius:50%;background:#cfcfcf}
.copyright{top:244px;width:1200px;text-align:center;font-size:11px;color:#bbb}
</style>
</head>
<body>

<header class="site-header abs">
  <div class="brand abs"><span class="brand-dot"></span>Bramblecrest finishing works</div>
  <div class="top-contact abs" style="left:420px">
    <span class="icon-circle"><svg width="16" height="16" viewBox="0 0 24 24"><path fill="#fff" d="M6.6 10.8a15 15 0 0 0 6.6 6.6l2.2-2.2c.3-.3.7-.4 1-.2 1.1.4 2.3.6 3.6.6.6 0 1 .4 1 1V20c0 .6-.4 1-1 1A17 17 0 0 1 3 4c0-.6.4-1 1-1h3.5c.6 0 1 .4 1 1 0 1.3.2 2.5.6 3.6.1.3 0 .7-.2 1z"/></svg></span>
    555.014.0187
  </div>
  <div class="top-contact abs" style="left:655px">
    <span class="icon-circle"><svg width="16" height="16" viewBox="0 0 24 24"><path fill="#fff" d="M3 5h18v14H3z"/><path fill="none" stroke="#0255a3" stroke-width="2" d="M3 6l9 7 9-7"/></svg></span>
    info@bramblecrestworks.com
  </div>
  <div class="top-social abs"><span></span><span></span><span></span><span></span></div>
  <nav class="main-nav abs">
    <span class="active">Home</span><span>Coating</span><span>Laser Engraving</span><span>Laser Cutting</span><span>Part Marking</span><span>Contact Us</span>
  </nav>
</header>

<section class="hero abs" role="img" aria-label="Laser cutting machine throwing sparks in a workshop">
  <h1 class="hero-title abs">Bramblecrest<br>Finishing Works</h1>
  <p class="hero-sub abs">Coatings &nbsp;|&nbsp; Part Making &nbsp;|&nbsp; Engraving</p>
  <a class="btn abs">Get Started &nbsp;»</a>
  <div class="dots abs"><span class="on"></span><span></span><span></span><span></span></div>
</section>

<section class="partners abs">
  <span>Quillmere</span><span>Tandrelo</span><span>Orvasko</span><span>Fenwyckly</span><span>Zelbrook</span><span>Marrowind</span>
</section>

<section class="about">
  <h2 class="section-title about-title abs">About Us</h2>
  <div class="about-text abs">
    <p>Lorem ipsum dolor sit amet, consectetur adipiscing elit, sed do eiusmod tempor incididunt ut labore et dolore magna aliqua. Ut enim ad minim veniam, quis nostrud exercitation ullamco laboris nisi ut aliquip ex ea commodo consequat. Duis aute irure dolor in reprehenderit in voluptate velit esse cillum dolore eu fugiat nulla pariatur.</p>
    <p>Ut enim ad minim veniam, quis nostrud exercitation ullamco laboris nisi ut aliquip ex ea commodo consequat. Duis aute irure dolor in reprehenderit in voluptate velit esse cillum dolore eu fugiat nulla pariatur.</p>
  </div>
  <a class="btn abs">Read More</a>
  <div class="about-photo abs" role="img" aria-label="Laser engraving machine lit in blue working on a metal plate"></div>
</section>

<section class="what-we-do">
  <div class="wwd-photo abs" role="img" aria-label="Sparks flying from a metal grinding wheel"></div>
  <div class="wwd-box abs">
    <h3>Laborum et dolorum fuga</h3>
    <p>At vero eos et accusamus et iusto odio dignissimos ducimus qui blanditiis praesentium voluptatum deleniti atque corrupti quos dolores et quas molestias excepturi sint occaecati cupiditate non provident.</p>
    <span class="btn-outline">Read More</span>
  </div>
  <h2 class="section-title wwd-title abs">What We Do</h2>
  <ul class="wwd-list abs">
    <li>Laborum et dolorum fuga</li><li>Et dolorum fuga</li><li>Laborum et dolorum fuga</li><li>Dolorum fuga</li><li>Mpedit quo minus</li><li>Duo minus</li><li>At vero eos et accusamus</li><li>Eos et accusamus</li><li>Accusamus</li>
  </ul>
</section>

<section class="why">
  <h2 class="section-title why-title abs">Why Choose Us</h2>
  <p class="why-intro abs">Sed ut perspiciatis unde omnis iste natus error sit voluptatem accusantium doloremque laudantium, totam rem aperiam, eaque ipsa quae ab illo inventore veritatis et quasi architecto beatae vitae dicta sunt explicabo. Nemo.</p>

  <div class="feature abs" style="left:106px;top:2324px">
    <div class="icon"><svg width="44" height="44" viewBox="0 0 44 44" fill="none" stroke="#fff" stroke-width="2"><rect x="8" y="8" width="28" height="24"/><line x1="8" y1="14" x2="36" y2="14"/><rect x="13" y="19" width="8" height="8"/><line x1="24" y1="21" x2="32" y2="21"/><line x1="24" y1="26" x2="32" y2="26"/></svg></div>
    <h4>Accusamus<br>Et Iusto</h4>
    <p>Sed ut perspiciatis unde<br>omnis iste natus error sit voluptatem<br>accusantium doloremque laudan...</p>
  </div>
  <div class="feature abs" style="left:450px;top:2324px">
    <div class="icon"><svg width="44" height="44" viewBox="0 0 44 44" fill="none" stroke="#fff" stroke-width="2"><path d="M18 6h8v12l-4 6-4-6z"/><path d="M22 24v8"/><path d="M14 36h16"/><path d="M16 30l-4 2M28 30l4 2"/></svg></div>
    <h4>Perspiciatis<br>Unde</h4>
    <p>Sed ut perspiciatis unde<br>omnis iste natus error sit voluptatem<br>accusantium doloremque laudan...</p>
  </div>
  <div class="feature abs" style="left:794px;top:2324px">
    <div class="icon"><svg width="44" height="44" viewBox="0 0 44 44" fill="none" stroke="#fff" stroke-width="2"><path d="M10 34L34 10"/><path d="M10 10l24 24"/><rect x="28" y="6" width="10" height="10" transform="rotate(45 33 11)"/></svg></div>
    <h4>Vero Eos<br>Et Accusamus</h4>
    <p>Sed ut perspiciatis unde<br>omnis iste natus error sit voluptatem<br>accusantium doloremque laudan...</p>
  </div>
  <div class="feature abs" style="left:278px;top:2695px">
    <div class="icon"><svg width="44" height="44" viewBox="0 0 44 44" fill="none" stroke="#fff" stroke-width="2"><rect x="10" y="10" width="24" height="18"/><path d="M6 32h32"/><line x1="14" y1="22" x2="30" y2="22"/></svg></div>
    <h4>Harum<br>Quidem Rerum</h4>
    <p>Sed ut perspiciatis unde<br>omnis iste natus error sit voluptatem<br>accusantium doloremque laudan...</p>
  </div>
  <div class="feature abs" style="left:622px;top:2695px">
    <div class="icon"><svg width="44" height="44" viewBox="0 0 44 44" fill="none" stroke="#fff" stroke-width="2"><path d="M22 6l4 12 12 4-12 4-4 12-4-12-12-4 12-4z"/></svg></div>
    <h4>Nam<br>Libero Tempore</h4>
    <p>Sed ut perspiciatis unde<br>omnis iste natus error sit voluptatem<br>accusantium doloremque laudan...</p>
  </div>
</section>

<svg class="abs" style="top:3064px;left:0" width="1200" height="24" aria-hidden="true"><polygon points="0,6 590,6 590,8 0,18" fill="#0255a3"/></svg>
<section class="services abs">
  <h2 class="section-title services-title abs">Our Services</h2>
  <div class="service-grid abs">
    <div class="service" role="img" aria-label="Laser engraving head marking a surface"><span>Laser engraving</span></div>
    <div class="service" role="img" aria-label="Laser cutter slicing sheet metal"><span>Laser Cutting</span></div>
    <div class="service" role="img" aria-label="Part marking laser working on a component"><span>Part Marking</span></div>
    <div class="service" role="img" aria-label="Worker applying coating to a part"><span>Coatings</span></div>
  </div>
</section>
<svg class="abs" style="top:3586px;left:0" width="1200" height="24" aria-hidden="true"><polygon points="620,4 1200,4 1200,16" fill="#0255a3"/></svg>

<section class="testimonials">
  <h2 class="section-title test-title abs">Testimonials</h2>
  <span class="quote-mark abs" style="left:100px">“</span>
  <span class="quote-mark abs" style="left:1058px">”</span>
  <p class="test-text abs">Sed ut perspiciatis unde omnis iste natus error sit voluptatem accusantium doloremque laudantium, totam rem aperiam, eaque ipsa quae ab illo inventore veritatis et quasi architecto beatae vitae dicta sunt explicabo.</p>
  <div class="avatar abs" role="img" aria-label="Portrait of the client"></div>
  <p class="test-name abs">- DANA WHITFIELD</p>
</section>

<section class="contact-bar abs">
  <div class="contact-item abs" style="left:107px">
    <span class="icon-circle"><svg width="16" height="18" viewBox="0 0 24 24"><path fill="#fff" d="M12 2a7 7 0 0 0-7 7c0 5 7 13 7 13s7-8 7-13a7 7 0 0 0-7-7zm0 9.5a2.5 2.5 0 1 1 0-5 2.5 2.5 0 0 1 0 5z"/></svg></span>
    <span>Bramblecrest Finishing Works<br>118 W Ironwood Ave #4 Tempe, AZ 85281</span>
  </div>
  <div class="contact-item abs" style="left:547px">
    <span class="icon-circle"><svg width="16" height="16" viewBox="0 0 24 24"><path fill="#fff" d="M6.6 10.8a15 15 0 0 0 6.6 6.6l2.2-2.2c.3-.3.7-.4 1-.2 1.1.4 2.3.6 3.6.6.6 0 1 .4 1 1V20c0 .6-.4 1-1 1A17 17 0 0 1 3 4c0-.6.4-1 1-1h3.5c.6 0 1 .4 1 1 0 1.3.2 2.5.6 3.6.1.3 0 .7-.2 1z"/></svg></span>
    <span>555.014.0187</span>
  </div>
  <div class="contact-item abs" style="left:912px">
    <span class="icon-circle"><svg width="16" height="16" viewBox="0 0 24 24"><path fill="#fff" d="M2 11l20-8-8 20-3-9z"/></svg></span>
    <span>info@bramblecrestworks.com</span>
  </div>
</section>

<footer class="site-footer abs">
  <nav class="footer-nav abs"><span>Home</span><span>Coating</span><span>Laser engraving</span><span>Laser cutting</span><span>Part marking</span><span>Contact us</span></nav>
  <div class="footer-social abs"><span></span><span></span><span></span><span></span></div>
  <p class="cert-title abs">Certificate of Certification</p>
  <div class="certs abs"><span></span><span></span><span></span><span></span></div>
  <p class="copyright abs">© 2018 Copyrights Bramblecrest Finishing Works All Rights Reserved</p>
</footer>

</body>
</html>
```